Tech business card design

We need an amazing business card design for our new business 'Pexla' a marketing tech startup based in Sydney, Australia. We provide an online marketplace for businesses to search and buy advertising media, connect with service providers and learn more about marketing. We wish to communicate 'cool tech', reliability and professionalism and design based around our logo.

Target Market(s)

Business Owners

Contact Information for Business Card

Name
Position
Email Address
Website
Phone Number

Font styles to use
Other font styles liked:
• Avenir & Avenir Next

Colors

Designer to choose colors to be used in the design.

```html
<!DOCTYPE html>
<html lang="en">
<head>
<meta charset="utf-8">
<title>Pexla Business Card</title>
<link rel="stylesheet" href="https://fonts.googleapis.com/css2?family=Nunito+Sans:wght@400;600;800;900&display=swap">
<style>
  :root {
    --backdrop: #e3e5ec;
    --navy: #1c2048;
    --navy-soft: #262b58;
    --paper: #ffffff;
    --ink: #1c2048;
    --ink-muted: #4a4d66;
    --pattern-tint: #f1f2f6;
  }
  * { margin: 0; padding: 0; box-sizing: border-box; }
  html, body {
    width: 1200px; height: 797px; overflow: hidden;
    background: var(--backdrop);
    font-family: "Nunito Sans", "Avenir Next", sans-serif;
  }
  .stage {
    position: relative; width: 1200px; height: 797px;
    display: flex; align-items: center; justify-content: center; gap: 44px;
  }
  .card {
    position: relative; width: 520px; height: 300px; overflow: hidden;
    box-shadow: 0 10px 30px rgba(28, 32, 72, 0.18);
  }

  /* Back side */
  .card-back { background: var(--navy); }
  .card-back .wordmark-pattern {
    position: absolute; inset: 0;
    background: linear-gradient(135deg, var(--navy-soft), var(--navy) 60%, #181b3e);
  }
  .card-back .brand-name {
    position: absolute; left: 50%; top: 50%; transform: translate(-50%, -50%);
    font-weight: 900; font-size: 46px; letter-spacing: -1px; color: var(--paper);
  }

  /* Front side */
  .card-front { background: var(--paper); }
  .card-front .icon-pattern {
    position: absolute; left: 150px; top: 0; right: 0; bottom: 0;
    background: linear-gradient(120deg, var(--paper), var(--pattern-tint) 55%, var(--paper));
  }
  .card-front .brand-name {
    position: absolute; left: 40px; top: 118px;
    font-weight: 900; font-size: 74px; letter-spacing: -2px; line-height: 1;
    color: var(--ink);
  }
  .card-front .brand-name sup {
    font-size: 12px; font-weight: 900; letter-spacing: 0; vertical-align: 48px; margin-left: 3px;
  }
  .divider {
    position: absolute; left: 300px; top: 158px; bottom: 0;
    width: 3px; background: var(--ink);
  }
  .contact {
    position: absolute; left: 318px; top: 62px; color: var(--ink);
  }
  .contact .person-name {
    font-weight: 800; font-size: 19px; letter-spacing: 0.5px; text-transform: uppercase;
  }
  .contact .person-role {
    font-size: 12px; color: var(--ink-muted); margin-bottom: 8px;
  }
  .contact-list { list-style: none; }
  .contact-list li {
    display: flex; align-items: center; gap: 7px;
    font-size: 11.5px; line-height: 17px; color: var(--ink);
  }
  .contact-list svg { width: 10px; height: 10px; fill: var(--ink); flex: none; }
</style>
</head>
<body>
<main class="stage">
  <section class="card card-back" aria-label="Card back">
    <div class="wordmark-pattern" role="img" aria-label="Repeating tonal brand-name pattern on navy"></div>
    <div class="brand-name">Pexla</div>
  </section>

  <section class="card card-front" aria-label="Card front">
    <div class="icon-pattern" role="img" aria-label="Faint line-icon pattern of marketing symbols"></div>
    <div class="brand-name">Pexla<sup>TM</sup></div>
    <div class="divider"></div>
    <div class="contact">
      <div class="person-name">Marcus Reed</div>
      <div class="person-role">Managing Director</div>
      <ul class="contact-list">
        <li>
          <svg viewBox="0 0 10 10" aria-hidden="true"><path d="M2 0.5 L3.6 0.5 L4.2 3 L3 3.8 Q4 6 6.2 7 L7 5.8 L9.5 6.4 L9.5 8 Q9.5 9.5 8 9.5 Q0.5 9 0.5 2 Q0.5 0.5 2 0.5Z"/></svg>
          000-987-6543
        </li>
        <li>
          <svg viewBox="0 0 10 10" aria-hidden="true"><path d="M0.5 2 H9.5 V8.5 H0.5Z M1.3 2.6 L5 5.5 L8.7 2.6" stroke="#fff" stroke-width="0.8"/></svg>
          info@pexlamail.com
        </li>
        <li>
          <svg viewBox="0 0 10 10" aria-hidden="true"><circle cx="5" cy="5" r="4.5"/><path d="M0.5 5 H9.5 M5 0.5 Q2.5 5 5 9.5 M5 0.5 Q7.5 5 5 9.5" stroke="#fff" stroke-width="0.7" fill="none"/></svg>
          www.pexla.com
        </li>
      </ul>
    </div>
  </section>
</main>
</body>
</html>
```